Kestrel - Transport company looking for a basic but smart design for the sides of our trailers

We have a logo 'Kestrel' which i would like to keep.
We have 2 companies Kestrel Haulage - Maroon signwriting (general freight ) and Kestrel Refrigerated - Blue signwriting (refrigerated freight) that can share the same design.
I'd like to come up with a basic modern design that will incorporate the Kestrel logo, the company name and the website and maybe an image at the front od some sort, a 3D swish or a stripe or something.
The Kestrel Haulage maroon trailers are too busy and I don't like the icicles on the front of the Kestrel Refrigerated blue trailers.

```html
<!DOCTYPE html>
<html lang="en">
<head>
<meta charset="utf-8">
<title>Kestrel Haulage – Trailer Side Design</title>
<link href="https://fonts.googleapis.com/css2?family=Russo+One&display=swap" rel="stylesheet">
<style>
  :root {
    --canvas-bg: #ffffff;
    --brand-maroon: #b04a3c;
    --red-deep: #a9242b;
    --red-main: #c8323a;
    --red-light: #dc4a4f;
  }
  html, body {
    margin: 0;
    padding: 0;
    overflow: hidden;
    background: var(--canvas-bg);
  }
  .trailer-side {
    position: relative;
    width: 1200px;
    height: 249px;
    overflow: hidden;
    background: var(--canvas-bg);
  }
  .brand-name {
    margin: 0;
    font-family: "Russo One", "Arial Black", sans-serif;
    font-weight: 400;
    color: var(--brand-maroon);
    text-transform: uppercase;
  }
  .brand-name__primary,
  .brand-name__secondary {
    position: absolute;
    display: block;
    line-height: 1;
    white-space: nowrap;
  }
  .brand-name__primary {
    left: 72px;
    top: 68px;
    font-size: 86px;
    letter-spacing: 1px;
  }
  .brand-name__secondary {
    left: 88px;
    top: 140px;
    font-size: 56px;
    letter-spacing: 9px;
  }
  .corner-graphic {
    position: absolute;
    top: 0;
    left: 0;
    width: 1200px;
    height: 249px;
  }
</style>
</head>
<body>
  <main class="trailer-side">
    <h1 class="brand-name">
      <span class="brand-name__primary">Kestrel</span>
      <span class="brand-name__secondary">Haulage</span>
    </h1>

    <svg class="corner-graphic" viewBox="0 0 1200 249" role="img" aria-label="Red angular corner graphic at the front of the trailer">
      <defs>
        <linearGradient id="corner-shadow" x1="0" y1="0" x2="1" y2="0">
          <stop offset="0" stop-color="#ffffff" stop-opacity="0"/>
          <stop offset="1" stop-color="#d4d4d4"/>
        </linearGradient>
        <linearGradient id="corner-red" x1="0" y1="1" x2="1" y2="0">
          <stop offset="0" stop-color="var(--red-deep)"/>
          <stop offset="0.55" stop-color="var(--red-main)"/>
          <stop offset="1" stop-color="var(--red-light)"/>
        </linearGradient>
      </defs>
      <polygon points="1000,0 1100,0 834,249 730,249" fill="url(#corner-shadow)"/>
      <polygon points="1100,0 1200,0 1200,249 834,249" fill="url(#corner-red)"/>
    </svg>
  </main>
</body>
</html>
```